dobbo's business card for earthmoving and tipper hire business.

I have a small earthmoving and tipper truck company. I am aiming for the smaller jobs that the big guys don't want. I am also Doing grass slashing and fire hazard reduction work. I would like to see some earthy colors, greens browns etc. I have a tractor with a front end loader attachment, and a 22 ton tipper. I would like to maybe have a silhouette of a tipper and tractor/slasher/loader setup in centre with my business name over the top and details to one side or something like that

Industry/Entity Type

Business

Contact Information for Business Card

Dobbo's small earthworks and tipper hireToowoombaABN: 47781050480PH 0479126773Email dobbo.3@farrowpost.com

Font styles to use
Sans Serif

Colors
fbee3d
abd036
85cae6
f78f20

Requirements
Nice to have
• Earthy colors . business name in blue

```html
<!DOCTYPE html>
<html lang="en">
<head>
<meta charset="utf-8">
<title>Dobbo's business card</title>
<link rel="stylesheet" href="https://fonts.googleapis.com/css2?family=Cabin:ital,wght@0,400;0,600;0,700;1,400&family=Josefin+Sans:wght@400&display=swap">
<style>
  :root{
    --paper:#ffffff;
    --green:#23a049;
    --green-soft:#4f9e47;
    --olive:#6e9650;
    --red:#98351f;
    --brown:#7a3d26;
    --brown-dark:#45291d;
    --sky:#a9d6ec;
    --ink-light:#f4f1ea;
    --machine-shade:#3f6a3d;
    --machine-light:#c8d4c0;
  }
  *{margin:0;padding:0;box-sizing:border-box}
  html,body{width:1007px;height:1200px;overflow:hidden;background:var(--paper)}
  body{position:relative;font-family:"Cabin",sans-serif}
  .card{position:absolute;left:19px;width:968px;overflow:hidden}
  .card--front{top:0;height:593px}
  .card--back{top:607px;height:593px}
  .card-bg{position:absolute;inset:0;width:100%;height:100%}
  .machine{position:absolute;border-radius:6px}
  .machine--faded{background:var(--machine-shade);opacity:.55}
  .machine--light{background:linear-gradient(180deg,var(--machine-light),#9fb39a);opacity:.85}
  .brand-name{position:absolute;color:var(--sky);font-weight:600;line-height:1}
  .front-name{left:327px;width:566px;text-align:center;top:342px;font-size:132px;letter-spacing:2px}
  .front-tagline{position:absolute;left:327px;width:566px;text-align:center;top:462px;font-family:"Josefin Sans",sans-serif;font-variant:small-caps;
    font-size:27px;letter-spacing:6px;color:var(--ink-light);white-space:nowrap}
  .back-name{left:330px;width:480px;text-align:center;top:34px;font-size:60px}
  .back-tagline{position:absolute;left:400px;top:82px;width:360px;height:70px}
  .info-box{position:absolute;top:337px;width:410px;height:220px;box-shadow:3px 4px 8px rgba(0,0,0,.45)}
  .contact-box{left:33px;background:#52a34a}
  .contact-head{height:94px;background:var(--olive);text-align:center;color:var(--ink-light);padding-top:6px}
  .contact-name{color:var(--sky);font-weight:700;font-size:26px;letter-spacing:6px;line-height:1.1}
  .contact-line{font-style:italic;font-size:14px;letter-spacing:2px;line-height:1.25}
  .contact-town,.contact-abn{font-weight:700;font-size:14px;letter-spacing:3px;line-height:1.3}
  .contact-body{padding:24px 0 0 30px;color:var(--ink-light);font-weight:700}
  .contact-phone{font-size:28px;letter-spacing:1px;white-space:nowrap}
  .contact-phone span{letter-spacing:8px}
  .contact-email{font-size:22px;margin-top:10px;letter-spacing:.3px;white-space:nowrap}
  .services-box{left:512px;background:linear-gradient(160deg,#3ea34b,#5c9a46)}
  .services{list-style:none;padding:2px 0 0 78px;color:var(--ink-light)}
  .service{display:flex;align-items:center;gap:8px;height:54px;font-size:26px;white-space:nowrap}
  .service--bold{font-weight:700}
  .service svg{width:36px;height:32px;flex:none}
</style>
</head>
<body>

<section class="card card--front">
  <svg class="card-bg" viewBox="0 0 968 593" preserveAspectRatio="none">
    <defs>
      <linearGradient id="soil-front" x1="0" y1="0" x2="0" y2="1">
        <stop offset="0" stop-color="#8a4327"/>
        <stop offset="1" stop-color="var(--brown-dark)"/>
      </linearGradient>
    </defs>
    <rect width="968" height="593" fill="var(--green)"/>
    <path d="M150,0 C300,80 460,130 610,124 C760,118 880,75 968,48 L968,0 Z" fill="var(--red)"/>
    <path d="M0,200 C320,240 700,255 968,370 L968,593 L0,593 Z" fill="url(#soil-front)"/>
  </svg>
  <div class="machine machine--faded" style="left:65px;top:66px;width:198px;height:150px" role="img" aria-label="Faded tipper truck cab silhouette"></div>
  <div class="brand-name front-name">Dobbo's</div>
  <div class="front-tagline">Earthworks and tipper hire</div>
</section>

<section class="card card--back">
  <svg class="card-bg" viewBox="0 0 968 593" preserveAspectRatio="none">
    <defs>
      <linearGradient id="soil-back" x1="0" y1="0" x2="0" y2="1">
        <stop offset="0" stop-color="#9a3b22"/>
        <stop offset="1" stop-color="#6e3222"/>
      </linearGradient>
    </defs>
    <rect width="968" height="593" fill="var(--green)"/>
    <path d="M130,0 C300,90 500,150 650,150 C800,150 900,112 968,86 L968,0 Z" fill="var(--red)"/>
    <path d="M0,222 C320,250 700,270 968,340 L968,593 L0,593 Z" fill="url(#soil-back)"/>
  </svg>
  <div class="machine machine--faded" style="left:17px;top:47px;width:192px;height:132px" role="img" aria-label="Faded tipper truck silhouette"></div>
  <div class="machine machine--light" style="left:243px;top:147px;width:356px;height:152px" role="img" aria-label="Tractor with front end loader"></div>
  <div class="machine machine--light" style="left:623px;top:139px;width:230px;height:190px" role="img" aria-label="Tipper truck"></div>

  <div class="brand-name back-name">Dobbo's</div>
  <svg class="back-tagline" viewBox="0 0 360 70">
    <path id="tagline-arc" d="M8,38 Q180,10 352,52" fill="none"/>
    <text font-family="Josefin Sans, sans-serif" font-size="24" fill="var(--ink-light)" letter-spacing="2" style="font-variant:small-caps">
      <textPath href="#tagline-arc">Earthworks and tipper hire</textPath>
    </text>
  </svg>

  <div class="info-box contact-box">
    <div class="contact-head">
      <div class="contact-name">Dobbo's</div>
      <div class="contact-line">small earthworks and tipper hire</div>
      <div class="contact-town">KELBROOK</div>
      <div class="contact-abn">ABN:51603928174</div>
    </div>
    <div class="contact-body">
      <div class="contact-phone">Phone: <span>0412583906</span></div>
      <div class="contact-email">Email dobbo.3@farrowpost.com</div>
    </div>
  </div>

  <div class="info-box services-box">
    <ul class="services">
      <li class="service">
        <svg viewBox="0 0 36 32" fill="none" stroke="var(--ink-light)" stroke-width="2"><rect x="6" y="4" width="10" height="10"/><path d="M16 14h10v6"/><circle cx="10" cy="22" r="7"/><circle cx="28" cy="25" r="4"/></svg>
        Earthmoving
      </li>
      <li class="service service--bold">
        <svg viewBox="0 0 36 32" fill="none" stroke="var(--ink-light)" stroke-width="2"><path d="M2 22V12h8l4-5h10v15z"/><path d="M24 10h10v12H24"/><circle cx="9" cy="24" r="3"/><circle cx="28" cy="24" r="3"/></svg>
        Tipper hire
      </li>
      <li class="service">
        <svg viewBox="0 0 36 32" fill="none" stroke="var(--ink-light)" stroke-width="2.5" stroke-linecap="round"><path d="M6 30C6 20 3 10 1 4"/><path d="M13 30C13 18 16 8 22 2"/><path d="M20 30C22 20 27 12 34 8"/></svg>
        Grass slashing
      </li>
      <li class="service service--bold">
        <svg viewBox="0 0 36 32" fill="none" stroke="var(--ink-light)" stroke-width="2"><circle cx="18" cy="17" r="14"/><path d="M18 26c-5 0-7-4-5-8 1-2 3-3 3-7 4 3 8 7 7 11-1 3-3 4-5 4z" fill="var(--ink-light)"/></svg>
        Fire hazard reduction
      </li>
    </ul>
  </div>
</section>

</body>
</html>
```